Modern Verdell Tree Care Website

I need a website for a full service Tree Care company. The company provides tree pruning, tree removal, tree preservation, emergency services, stump grinding, and emergency tree services.

Target Market(s)

Customers that need tree services

Industry/Entity Type

Landscaping, Tree Services

Coding

Coded - Design and coding required

Number of Pages Required

5+ page

Font styles to use
Sans Serif

Requirements
Must have
• Good clean design that showcases the services the company provides.
Nice to have
• Services page; contact form, blog, home page, about page

```html
<!DOCTYPE html>
<html lang="en">
<head>
<meta charset="utf-8">
<title>Verdell Tree Care</title>
<link rel="stylesheet" href="https://fonts.googleapis.com/css2?family=Poppins:wght@400;500;600;700&display=swap">
<style>
:root{
  --green:#8cc63f;
  --green-dark:#6ea52a;
  --orange:#f7a93a;
  --tan:#c89a64;
  --ink:#2f2f2f;
  --muted:#555;
  --light:#f0f0f0;
  --mint:#eef5e0;
  --white:#fff;
}
*{box-sizing:border-box;margin:0;padding:0}
html,body{width:1200px;height:3900px;overflow:hidden}
body{font-family:'Poppins',sans-serif;color:var(--ink);background:var(--white);position:relative}
.abs{position:absolute}
.btn{position:absolute;display:flex;align-items:center;justify-content:center;border-radius:30px;font-weight:600;color:var(--white);text-transform:uppercase}
.btn-orange{background:var(--orange)}
.btn-green{background:var(--green)}
.rule{position:absolute;height:3px;width:52px;background:var(--orange)}
.rule-green{background:var(--green)}

/* header */
.site-header{position:absolute;left:0;top:0;width:1200px;height:86px;background:var(--white)}
.brand{position:absolute;left:136px;top:22px;display:flex;align-items:center;gap:12px}
.brand-mark{width:38px;height:38px;background:var(--green)}
.brand-name{font-size:24px;font-weight:600;color:var(--ink)}
.main-nav{position:absolute;top:32px;left:458px;display:flex;gap:0}
.main-nav a{position:absolute;font-size:15px;font-weight:600;color:var(--ink);text-decoration:none;white-space:nowrap}
.main-nav a.active{color:var(--green)}
.main-nav a.active::after{content:"";position:absolute;left:0;right:0;top:30px;height:3px;background:var(--green)}

/* hero */
.hero{position:absolute;left:0;top:86px;width:1200px;height:680px;background:linear-gradient(110deg,#5e7a3a 0%,#7f9a48 35%,#4f7a2a 65%,#86a94a 100%)}
.hero-title{position:absolute;left:0;width:1200px;top:140px;text-align:center;font-size:72px;font-weight:700;color:var(--white);letter-spacing:-1px}
.hero-sub{position:absolute;left:0;width:1200px;top:236px;text-align:center;font-size:25px;color:var(--white)}
.hero .btn{left:493px;top:289px;width:202px;height:52px;font-size:18px}
.hero-curve{position:absolute;left:0;top:670px}

/* about */
.about-visual{position:absolute;left:163px;top:840px;width:337px;height:337px;background:linear-gradient(135deg,#d9a56b 0%,#f29a2e 50%,#7cbd3a 100%)}
.about-title{position:absolute;left:582px;top:832px;font-size:42px;font-weight:600}
.about-text{position:absolute;left:582px;top:914px;width:500px;font-size:17px;line-height:24px;color:var(--ink)}
.about .btn{left:579px;top:1154px;width:200px;height:53px;font-size:18px}

/* services */
.services{position:absolute;left:0;top:1321px;width:1200px;height:660px;background:var(--green)}
.section-title{position:absolute;left:0;width:1200px;text-align:center;font-size:42px;font-weight:600}
.services .section-title{top:66px;color:var(--white)}
.services .rule{left:574px;top:123px}
.service-card{position:absolute;top:172px;width:312px;height:351px;background:var(--white);border-radius:4px;text-align:center}
.service-photo{width:100%;height:215px}
.service-card h3{font-size:19px;font-weight:500;margin-top:18px}
.service-card p{font-size:13.5px;line-height:20px;color:var(--muted);margin:8px 18px 0}
.slider-arrow{position:absolute;top:318px}
.services-curve{position:absolute;left:0;top:1900px}

/* why */
.why{position:absolute;left:0;top:1967px;width:1200px;height:552px;background:var(--light)}
.why-title{position:absolute;left:124px;top:112px;font-size:42px;font-weight:600}
.why .rule{left:124px;top:171px}
.why-list{position:absolute;list-style:none;font-size:16.5px;font-weight:500}
.why-list li{height:44px;display:flex;align-items:flex-start;gap:8px}
.why .btn{left:121px;top:416px;width:200px;height:53px;font-size:18px}
.why-photo{position:absolute;left:683px;top:2004px;width:440px;height:440px;border-radius:50%;background:radial-gradient(circle at 55% 45%,#d9dcd6 0%,#9aa293 60%,#6b7259 100%)}
.why-arc{position:absolute;left:672px;top:1990px}

/* blogs */
.blogs .section-title{top:2592px}
.blogs .rule{left:574px;top:2650px}
.blog-card{position:absolute;top:2684px;width:315px;height:368px;background:var(--white);border:1px solid #cfcfcf}
.blog-photo{width:100%;height:195px}
.blog-card h3{font-size:15px;font-weight:600;line-height:21px;margin:20px 32px 0}
.blog-card p{font-size:12px;line-height:16px;color:var(--muted);margin:10px 34px 0}
.blog-card .btn{position:static;width:133px;height:35px;font-size:12px;margin:12px 0 0 38px}

/* contact */
.contact{position:absolute;left:0;top:3137px;width:1200px;height:555px;background:linear-gradient(180deg,#f3b02e 0%,#f4b33c 100%)}
.contact .section-title{top:92px;color:var(--white)}
.contact .rule{left:566px;top:150px;width:70px;background:var(--white)}
.field{position:absolute;background:var(--white);font-size:14px;color:#888;padding:0 24px;display:flex;align-items:center}
.field-area{align-items:flex-start;padding-top:22px}
.send{position:absolute;left:510px;top:419px;width:188px;height:50px;border:3px solid var(--white);border-radius:30px;color:var(--white);font-size:14px;font-weight:600;display:flex;align-items:center;justify-content:center}

/* footer */
.footer-nav a{position:absolute;top:3747px;font-size:15px;font-weight:600;color:var(--ink);text-decoration:none}
.footer-call{position:absolute;left:784px;top:3744px;font-size:15px;display:flex;gap:8px}
.footer-call b{font-weight:700}
.footer-phone2{position:absolute;left:914px;top:3768px;font-size:15px;font-weight:700}
.footer-bar{position:absolute;left:0;top:3820px;width:1200px;height:80px;background:var(--mint)}
.copyright{position:absolute;left:118px;top:32px;font-size:13.5px}
.social{position:absolute;top:18px;width:40px;height:40px;border:2px solid var(--green);border-radius:50%}
</style>
</head>
<body>

<header class="site-header">
  <div class="brand"><span class="brand-mark"></span><span class="brand-name">Verdell Tree Care</span></div>
  <nav class="main-nav">
    <a class="active" style="left:0">HOME</a>
    <a style="left:98px">ABOUT</a>
    <a style="left:200px">SERVICES</a>
    <a style="left:322px">BLOGS</a>
    <a style="left:422px">REVIEWS</a>
    <a style="left:538px">CONTACT</a>
  </nav>
</header>

<section class="hero" role="img" aria-label="Arborist trimming a green hedge with a hedge trimmer">
  <h1 class="hero-title">WELCOME TO VERDELL</h1>
  <p class="hero-sub">Serving Marrowfield and surrounding areas.</p>
  <span class="btn btn-orange">Contact Us</span>
</section>
<svg class="hero-curve" width="1200" height="100" viewBox="0 0 1200 100">
  <path d="M0 95 Q600 -50 1200 80 L1200 100 L0 100 Z" fill="var(--green)"/>
  <path d="M0 100 Q600 -30 1200 90 L1200 100 Z" fill="var(--white)"/>
</svg>

<section class="about">
  <div class="about-visual" role="img" aria-label="Tree artwork in wood, orange and grass tones"></div>
  <h2 class="about-title">ABOUT VERDELL</h2>
  <p class="about-text">At Verdell Tree Care, we are more than just a tree service company, we are stewards of our beautiful trees. With a passion deeply rooted in arboriculture, we embark on a mission to promote the health, beauty, and safety of your trees and landscapes. Whether it's expert tree trimming to enhance aesthetics, meticulous tree removal to mitigate hazards, or comprehensive tree health assessments to ensure safety , we approach each task with unwavering dedication and attension to detail.</p>
  <span class="btn btn-orange">Learn More</span>
</section>

<section class="services">
  <h2 class="section-title">OUR SERVICES</h2>
  <span class="rule"></span>
  <svg class="slider-arrow" style="left:40px" width="28" height="40" viewBox="0 0 28 40"><path d="M22 4 L6 20 L22 36" fill="none" stroke="#fff" stroke-width="5"/></svg>
  <svg class="slider-arrow" style="left:1133px" width="28" height="40" viewBox="0 0 28 40"><path d="M6 4 L22 20 L6 36" fill="none" stroke="#fff" stroke-width="5"/></svg>
  <article class="service-card" style="left:112px">
    <div class="service-photo" role="img" aria-label="Climber cutting branches high in a tree" style="background:linear-gradient(135deg,#3e5a1e,#7ba63a)"></div>
    <h3>TREE REMOVAL</h3>
    <p>Lorem ipsum dolor sit amet, consectetur adipiscing elit, sed do eiusmod</p>
  </article>
  <article class="service-card" style="left:449px">
    <div class="service-photo" role="img" aria-label="Pruning loppers cutting a branch" style="background:linear-gradient(135deg,#4d6b2a,#9aa49a)"></div>
    <h3>TREE PRUNING</h3>
    <p>Lorem ipsum dolor sit amet, consectetur adipiscing elit, sed do eiusmod</p>
  </article>
  <article class="service-card" style="left:785px">
    <div class="service-photo" role="img" aria-label="Stump grinder working on a tree stump" style="background:linear-gradient(135deg,#8a3a2a,#c99a58)"></div>
    <h3>STUMP GRINDING</h3>
    <p>Lorem ipsum dolor sit amet, consectetur adipiscing elit, sed do eiusmod</p>
  </article>
</section>
<svg class="services-curve" width="1200" height="80" viewBox="0 0 1200 80">
  <path d="M0 70 Q600 -20 1200 70 L1200 80 L0 80 Z" fill="var(--tan)"/>
  <path d="M0 80 Q600 -8 1200 80 Z" fill="var(--light)"/>
</svg>

<section class="why">
  <h2 class="why-title">WHY CHOOSE VERDELL</h2>
  <span class="rule rule-green"></span>
  <ul class="why-list" style="left:121px;top:218px">
    <li><svg width="18" height="18" viewBox="0 0 18 18"><path d="M2 9 L7 14 L16 4" fill="none" stroke="var(--green)" stroke-width="3"/></svg>Licensed and Insured</li>
    <li><svg width="18" height="18" viewBox="0 0 18 18"><path d="M2 9 L7 14 L16 4" fill="none" stroke="var(--green)" stroke-width="3"/></svg>24 Hours Emergency services</li>
    <li><svg width="18" height="18" viewBox="0 0 18 18"><path d="M2 9 L7 14 L16 4" fill="none" stroke="var(--green)" stroke-width="3"/></svg>Locally Owned &amp; Operated</li>
    <li><svg width="18" height="18" viewBox="0 0 18 18"><path d="M2 9 L7 14 L16 4" fill="none" stroke="var(--green)" stroke-width="3"/></svg>Professional Work</li>
  </ul>
  <ul class="why-list" style="left:419px;top:218px">
    <li><svg width="18" height="18" viewBox="0 0 18 18"><path d="M2 9 L7 14 L16 4" fill="none" stroke="var(--green)" stroke-width="3"/></svg>Safety is our No. 1 Priority</li>
    <li><svg width="18" height="18" viewBox="0 0 18 18"><path d="M2 9 L7 14 L16 4" fill="none" stroke="var(--green)" stroke-width="3"/></svg>Free Estimates</li>
    <li><svg width="18" height="18" viewBox="0 0 18 18"><path d="M2 9 L7 14 L16 4" fill="none" stroke="var(--green)" stroke-width="3"/></svg>Licensed Arborist on Staff</li>
  </ul>
  <span class="btn btn-green">Learn More</span>
</section>
<svg class="why-arc" width="460" height="460" viewBox="0 0 460 460">
  <path d="M120 40 A220 220 0 1 1 230 450" fill="none" stroke="var(--orange)" stroke-width="20"/>
</svg>
<div class="why-photo" role="img" aria-label="Arborist in safety gear cutting a trunk with a chainsaw"></div>

<section class="blogs">
  <h2 class="section-title">LATEST BLOGS</h2>
  <span class="rule rule-green"></span>
  <article class="blog-card" style="left:121px">
    <div class="blog-photo" role="img" aria-label="Hand pruning a leafy branch with shears" style="background:linear-gradient(135deg,#9cc35a,#4f7a2a)"></div>
    <h3>LOREM IPSUM DOLOR SIT AMET, CONSECTETUR ADIPISCIN</h3>
    <p>Sed ut perspiciatis unde omnis iste natus error sit voluptatem accusantium</p>
    <span class="btn btn-orange">Learn More</span>
  </article>
  <article class="blog-card" style="left:457px">
    <div class="blog-photo" role="img" aria-label="Climber with chainsaw on a tree trunk" style="background:linear-gradient(135deg,#5f7e3a,#a7a08a)"></div>
    <h3>LOREM IPSUM DOLOR SIT AMET, CONSECTETUR ADIPISCIN</h3>
    <p>Sed ut perspiciatis unde omnis iste natus error sit voluptatem accusantium</p>
    <span class="btn btn-orange">Learn More</span>
  </article>
  <article class="blog-card" style="left:794px">
    <div class="blog-photo" role="img" aria-label="Chainsaw cutting into a tree trunk" style="background:linear-gradient(135deg,#7e7a6e,#4a3a2a)"></div>
    <h3>LOREM IPSUM DOLOR SIT AMET, CONSECTETUR ADIPISCIN</h3>
    <p>Sed ut perspiciatis unde omnis iste natus error sit voluptatem accusantium</p>
    <span class="btn btn-orange">Learn More</span>
  </article>
</section>

<section class="contact" role="img" aria-label="Orange-toned photo of tree work behind the contact form">
  <h2 class="section-title">OUR SERVICES</h2>
  <span class="rule"></span>
  <div class="field" style="left:219px;top:166px;width:379px;height:54px">Name*</div>
  <div class="field" style="left:607px;top:166px;width:378px;height:54px">Email address*</div>
  <div class="field" style="left:219px;top:234px;width:379px;height:56px">Phone*</div>
  <div class="field" style="left:607px;top:234px;width:378px;height:56px">Company Name*</div>
  <div class="field field-area" style="left:219px;top:302px;width:766px;height:91px">Type Message</div>
  <span class="send">SEND MESSAGE</span>
</section>

<footer>
  <nav class="footer-nav">
    <a style="left:121px">HOME</a>
    <a style="left:217px">ABOUT</a>
    <a style="left:317px">SERVICES</a>
    <a style="left:435px">BLOGS</a>
    <a style="left:533px">REVIEWS</a>
    <a style="left:647px">CONTACT</a>
  </nav>
  <div class="footer-call">
    <svg width="18" height="18" viewBox="0 0 24 24"><path d="M6 3 L10 7 L8 10 Q10 14 14 16 L17 14 L21 18 L18 21 Q9 20 3 6 Z" fill="var(--green)"/></svg>
    <span>CALL US NOW</span><b>(555) 014 2739</b>
  </div>
  <div class="footer-phone2">(555) 016-9939</div>
  <div class="footer-bar">
    <p class="copyright">© 2024 Company Name | All Rights Reserved</p>
    <span class="social" style="left:936px"></span>
    <span class="social" style="left:982px"></span>
    <span class="social" style="left:1026px"></span>
  </div>
</footer>

</body>
</html>
```